Website Design for WestaKolory.pl – Luxury Wedding Car Rental with Chauffeur

We are looking for a talented designer to create a modern, elegant, and fully responsive website for our new brand – WestyKolory.pl. We are a premium car rental platform in Poland, offering luxury and exotic vehicles exclusively for weddings. All cars come with a professional chauffeur, ensuring a high-end, stress-free, and stylish experience.
Website Purpose:
The website should present our offering in a luxurious, clear, and inspiring way. It must build trust, highlight the prestige of our brand, and encourage inquiries. Our target audience includes engaged couples, wedding planners, and clients seeking a truly exceptional vehicle for their special day.
Design Requirements:
Style: modern, elegant, minimalist
Color palette: white, black, gold, optionally silver – refined and luxurious
Typography: clean, modern, high-end
Layout: clear, intuitive, with large car images and well-defined sections
Fully responsive (desktop, tablet, mobile)
Bilingual layout (Polish/English) must be considered
Pages to Design:
Homepage
About Us
Fleet Overview
Individual Car Pages
Services (Weddings, Photo Shoots, Film Rentals)
Why Us / Unique Selling Points
Contact
FAQ
Inspiration:
Luxury automotive brands (e.g. Varnel-Hoske, Corvash, Elbrin Tusko)
High-end wedding websites
Minimalist layouts with large visuals and elegant typography
Additional Notes:
The design should evoke the emotions of a wedding day – elegance, uniqueness, style, and class. Please avoid flashy colors, excessive graphic effects, or overly decorative elements. Subtlety, prestige, and sophistication are key.

```html
<!DOCTYPE html>
<html lang="en">
<head>
<meta charset="utf-8">
<title>WestaKolory.pl – Luxury Wedding Cars</title>
<link rel="stylesheet" href="https://fonts.googleapis.com/css2?family=Libre+Baskerville:ital,wght@0,400;0,700;1,400&family=Poppins:ital,wght@0,400;0,500;0,600;1,400&display=swap">
<style>
:root{
  --navy:#1b2740;
  --gold:#d4b44a;
  --ink:#1c1c1c;
  --muted:#555;
  --line:#e6e6e6;
  --white:#fff;
}
*{box-sizing:border-box;margin:0;padding:0}
html,body{width:1200px;height:4942px;overflow:hidden}
body{position:relative;background:var(--white);font-family:"Poppins",sans-serif;color:var(--ink)}
.abs{position:absolute}
.serif{font-family:"Libre Baskerville",serif}
.guide{position:absolute;top:75px;width:1px;height:4500px;background:#f0f0f0}
.header{position:absolute;top:0;left:0;width:1200px;height:75px;border-bottom:1px solid var(--line);background:#fff}
.brand{position:absolute;left:86px;top:22px;font-family:"Libre Baskerville",serif;font-size:24px;color:var(--gold);display:flex;align-items:center;gap:10px}
.brand .dot{width:14px;height:14px;border-radius:50%;background:var(--gold)}
.nav{position:absolute;left:466px;top:28px;display:flex;gap:22px;font-size:13px;color:#333;align-items:center}
.nav .home{width:14px;height:13px}
.btn{display:inline-flex;align-items:center;justify-content:center;font-size:12px;font-weight:600;letter-spacing:.3px;border:1.5px solid var(--navy);color:var(--navy);background:#fff;text-transform:uppercase}
.btn.dark{background:var(--navy);color:#fff}
.media{position:absolute}
.hero-title{left:134px;top:190px;font-size:49px;line-height:64px;font-weight:400;color:var(--ink);letter-spacing:-0.5px;white-space:nowrap}
.hero-lead{left:760px;top:192px;font-size:17px;line-height:27px;color:#444;width:320px}
.caption{font-style:italic;font-size:14px;color:#333}
.arrow-btn{position:absolute;width:36px;height:23px;display:flex;align-items:center;justify-content:center}
.h2{font-size:28px;line-height:38px;color:var(--ink);white-space:nowrap;letter-spacing:-0.3px}
.feature{position:absolute;top:1089px;height:126px;width:240px;padding:22px 10px 0 0;font-family:"Libre Baskerville",serif;font-size:11px;line-height:17px;text-transform:uppercase}
.feature svg{display:block;margin-bottom:12px}
.feature.active{background:var(--navy);color:#fff;padding:22px 10px 0 32px}
.label{color:var(--gold);font-size:14px;letter-spacing:.5px;font-weight:500}
.para{font-size:13.5px;line-height:21px;color:#555}
.svc{position:absolute;left:86px;width:452px;font-family:"Libre Baskerville",serif;font-size:14.5px;text-transform:uppercase;display:flex;justify-content:space-between;align-items:center;padding:0 24px 0 27px;border-bottom:1px solid var(--line);height:56px;white-space:nowrap}
.svc.active{background:var(--navy);color:#fff;height:107px;display:block;padding-top:20px;border:none;white-space:normal}
.svc.active p{font-family:"Poppins",sans-serif;text-transform:none;font-size:13px;line-height:20px;margin-top:10px;color:#e6e6e6}
.footer{position:absolute;left:0;top:4577px;width:1200px;height:365px;background:var(--navy);color:#fff}
.footer-title{font-family:"Libre Baskerville",serif;color:var(--gold);font-size:23px;font-weight:400;position:absolute}
.contact-line{position:absolute;left:113px;font-size:15px;display:flex;align-items:center;gap:8px}
.social{position:absolute;top:4725px;width:36px;height:36px;border-radius:50%;background:rgba(255,255,255,.12)}
</style>
</head>
<body>
<div class="guide" style="left:88px"></div>
<div class="guide" style="left:1110px"></div>

<header class="header">
  <div class="brand"><span class="dot"></span>WestaKolory</div>
  <nav class="nav">
    <svg class="home" viewBox="0 0 14 13"><path d="M7 0L0 6h2v7h4V9h2v4h4V6h2z" fill="var(--gold)"/></svg>
    <span>About Us</span><span>Fleet</span><span>Services</span><span>Why Us</span><span>FAQ</span><span>Contact</span>
    <span style="display:flex;align-items:center;gap:5px"><span style="width:11px;height:11px;border-radius:50%;background:var(--gold);display:inline-block"></span>EN ⌄</span>
  </nav>
  <a class="btn abs" style="left:954px;top:17px;width:158px;height:39px">Request a quote</a>
</header>

<!-- Hero -->
<h1 class="abs serif hero-title">ARRIVE IN<br>STYLE. CELEBRATE<br>IN ELEGANCE.</h1>
<p class="abs hero-lead">Luxury &amp; Exotic Wedding Cars with Chauffeur Service in Poland.</p>
<a class="btn dark abs" style="left:760px;top:267px;width:144px;height:38px;font-size:11px">View our fleet</a>
<a class="btn abs" style="left:908px;top:267px;width:128px;height:38px;font-size:11px">Get a quote</a>
<p class="abs caption" style="left:134px;top:405px">Our Most Desired Cars</p>
<div class="abs serif" style="left:1050px;top:374px;color:var(--gold);font-size:25px">01<span style="font-size:13px;color:#aaa"> /04</span></div>
<div class="media" role="img" aria-label="Vintage white wedding car with flowers and ribbons" style="left:115px;top:375px;width:1027px;height:547px;background:radial-gradient(ellipse at 55% 55%,#e9e4d8 0%,#d8d2c5 45%,#fff 72%)"></div>
<div class="arrow-btn" style="left:893px;top:833px;background:var(--navy)"><svg width="16" height="10"><path d="M16 5H2M6 1L2 5l4 4" stroke="#fff" fill="none" stroke-width="1.5"/></svg></div>
<div class="arrow-btn" style="left:931px;top:833px;background:var(--gold)"><svg width="16" height="10"><path d="M0 5h14M10 1l4 4-4 4" stroke="#fff" fill="none" stroke-width="1.5"/></svg></div>

<!-- Elevate -->
<h2 class="abs serif h2" style="left:129px;top:958px">ELEVATE YOUR<br>WEDDING EXPERIENCE</h2>
<p class="abs" style="left:129px;top:1043px;font-size:12.5px;color:#555">Luxury is not just about cars. It's about how we make you feel.</p>
<div class="feature" style="left:129px"><svg width="72" height="30" viewBox="0 0 72 30" fill="none" stroke="var(--gold)" stroke-width="1.5"><path d="M3 20l4-8h20l8-6h18l10 8 6 2v6H3z"/><circle cx="17" cy="24" r="4"/><circle cx="55" cy="24" r="4"/></svg>Luxury cars, spotless<br>and elegant</div>
<div class="feature" style="left:369px"><svg width="40" height="40" viewBox="0 0 40 40" fill="none" stroke="var(--gold)" stroke-width="1.5"><circle cx="13" cy="10" r="6"/><circle cx="27" cy="10" r="6"/><path d="M3 38V26a10 10 0 0 1 20 0v12M17 38V26a10 10 0 0 1 20 0v12"/></svg>Personalized service<br>for every couple</div>
<div class="feature active" style="left:580px"><svg width="40" height="40" viewBox="0 0 40 40" fill="none" stroke="var(--gold)" stroke-width="1.5"><circle cx="20" cy="14" r="8"/><path d="M12 10h16M6 38a14 14 0 0 1 28 0z"/><circle cx="20" cy="31" r="3"/></svg>Professional,<br>experienced chauffeurs</div>
<div class="feature" style="left:876px"><svg width="42" height="42" viewBox="0 0 42 42" fill="none" stroke="var(--gold)" stroke-width="1.5"><path d="M4 4l10 12M22 4l-8 12M4 4h18"/><circle cx="22" cy="28" r="11"/><path d="M22 21v7l5 3"/></svg>On-time, stress free,<br>stylish rides</div>

<!-- About -->
<div class="media" role="img" aria-label="Bride and groom beside a dark convertible among pine trees" style="left:0;top:1307px;width:599px;height:553px;background:linear-gradient(135deg,#8a7d55,#c9b597 45%,#4a4a3e)"></div>
<p class="abs label" style="left:689px;top:1391px">ABOUT US</p>
<h2 class="abs serif h2" style="left:689px;top:1418px;line-height:37px">CRAFTED<br>FOR UNFORGETTABLE<br>CELEBRATIONS</h2>
<p class="abs para" style="left:689px;top:1540px;width:395px">WestyKolory.pl, we believe that your wedding day deserves nothing less than perfection — and that includes how you arrive. A car is not just transportation — it's a statement, a moment in motion, a part of the story you'll tell for years to come.</p>
<p class="abs para" style="left:689px;top:1650px;width:395px">Born from a shared passion for automotive beauty and wedding elegance, our team handpicks only the most iconic vehicles — selected for their style.</p>
<a class="btn abs" style="left:689px;top:1734px;width:180px;height:40px;font-size:11px">Read more about us</a>

<!-- Collection -->
<div class="media" role="img" aria-label="Newlyweds beside a silver classic car in front of a stone building" style="left:121px;top:2012px;width:958px;height:471px;background:linear-gradient(160deg,#6f6453,#a9a294 50%,#4b463d)"></div>
<h2 class="abs serif" style="left:184px;top:1960px;font-size:43px;line-height:58px;color:var(--ink);white-space:nowrap;letter-spacing:-0.5px">EXPLORE OUR WEDDING<br><span style="color:var(--gold)">CAR COLLECTION</span></h2>
<div class="abs" style="left:184px;top:2237px;width:473px;height:163px;background:rgba(255,255,255,.22);padding:28px 32px;color:#fff">
  <div class="serif" style="font-size:24px">CLASSIC</div>
  <p style="font-size:13.5px;line-height:21px;margin-top:8px;color:#eee">Timeless elegance meets vintage charm. Ideal for traditional weddings, these iconic cars bring a sense of nostalgia and sophistication to your special day.</p>
</div>
<div class="abs" style="left:148px;top:2483px;width:906px;height:17px;background:#777"></div>

<!-- Services -->
<h2 class="abs serif" style="left:86px;top:2658px;font-size:29px;line-height:38px;white-space:nowrap;letter-spacing:-0.5px">TAILORED SERVICES<br>FOR EVERY CELEBRATION</h2>
<div class="svc active" style="top:2761px"><div style="display:flex;justify-content:space-between">WEDDING CAR RENTAL<svg width="20" height="12"><path d="M1 11C6 3 12 3 19 2M14 0l5 2-4 4" stroke="var(--gold)" fill="none" stroke-width="1.4"/></svg></div><p>Your grand entrance deserves a grand vehicle. Choose from our elegant fleet with chauffeur service included.</p></div>
<div class="svc" style="top:2875px">Engagement &amp; Pre-Wedding Shoots<svg width="20" height="12"><path d="M1 11C6 3 12 3 19 2M14 0l5 2-4 4" stroke="#333" fill="none" stroke-width="1.4"/></svg></div>
<div class="svc" style="top:2932px">Film &amp; Video Rentals<svg width="20" height="12"><path d="M1 11C6 3 12 3 19 2M14 0l5 2-4 4" stroke="#333" fill="none" stroke-width="1.4"/></svg></div>
<div class="svc" style="top:2988px;border-bottom:none">VIP Guest Transport<svg width="20" height="12"><path d="M1 11C6 3 12 3 19 2M14 0l5 2-4 4" stroke="#333" fill="none" stroke-width="1.4"/></svg></div>
<div class="media" role="img" aria-label="White luxury saloon decorated with a white floral bouquet" style="left:605px;top:2630px;width:537px;height:432px;background:radial-gradient(ellipse at 50% 50%,#c9cbcf 0%,#e6e7e9 50%,#fff 72%)"></div>

<!-- Video -->
<div class="media" role="img" aria-label="Couple embracing beside a silver vintage convertible in a forest" style="left:0;top:3160px;width:1200px;height:567px;background:linear-gradient(120deg,#5d5a3c,#a59f87 45%,#6a6148)"></div>
<div class="abs" style="left:545px;top:3387px;width:112px;height:112px;border-radius:50%;background:rgba(255,255,255,.55);display:flex;align-items:center;justify-content:center"><svg width="22" height="24"><path d="M2 1l19 11L2 23z" fill="#222"/></svg></div>

<!-- Testimonial -->
<div class="media" role="img" aria-label="Client portrait" style="left:548px;top:3820px;width:102px;height:102px;border-radius:50%;background:linear-gradient(#6d737a,#2e3238)"></div>
<div class="arrow-btn" style="left:109px;top:3971px;background:var(--navy)"><svg width="16" height="10"><path d="M16 5H2M6 1L2 5l4 4" stroke="#fff" fill="none" stroke-width="1.5"/></svg></div>
<div class="arrow-btn" style="left:1050px;top:3971px;background:var(--gold)"><svg width="16" height="10"><path d="M0 5h14M10 1l4 4-4 4" stroke="#fff" fill="none" stroke-width="1.5"/></svg></div>
<p class="abs serif" style="left:260px;top:3950px;width:680px;text-align:center;font-style:italic;font-size:23px;line-height:34px">"The car was a dream come true. Everyone turned their heads! The chauffeur was polite and professional stress-free experience from start to finish!"</p>
<div class="abs" style="left:115px;top:4143px;width:970px;height:1px;background:var(--line)"></div>

<!-- Book -->
<div class="media" role="img" aria-label="Silver estate car with wedding decorations before a mansion" style="left:190px;top:4239px;width:472px;height:256px;background:linear-gradient(140deg,#7b7466,#b9b4aa 50%,#5a564d)"></div>
<h2 class="abs serif h2" style="left:720px;top:4272px;font-size:30px">BOOK YOUR CAR</h2>
<p class="abs serif" style="left:720px;top:4318px;font-size:12px">YOUR DREAM CAR AWAITS</p>
<p class="abs para" style="left:720px;top:4352px;width:300px;font-size:13px">Tell us about your wedding day and let us take care of the journey.</p>
<a class="btn abs" style="left:720px;top:4412px;width:177px;height:42px;font-size:11px">Schedule your ride</a>

<!-- Footer -->
<footer class="footer"></footer>
<h4 style="left:113px;top:4676px" class="footer-title">CONTACT INFO</h4>
<div class="contact-line" style="top:4725px;color:#fff"><svg width="10" height="14"><path d="M5 0a5 5 0 0 0-5 5c0 4 5 9 5 9s5-5 5-9a5 5 0 0 0-5-5z" fill="var(--gold)"/><circle cx="5" cy="5" r="2" fill="var(--navy)"/></svg>Some goes address link here</div>
<div class="contact-line" style="top:4757px;color:#fff"><svg width="12" height="12"><path d="M2 0l3 3-2 2a8 8 0 0 0 4 4l2-2 3 3-2 2C5 12 0 7 0 2z" fill="var(--gold)"/></svg>012.345.6789</div>
<div class="contact-line" style="top:4789px;color:#fff"><svg width="13" height="10"><rect width="13" height="10" fill="var(--gold)"/><path d="M0 0l6.5 5L13 0" stroke="var(--navy)" fill="none"/></svg>Connect@example.com</div>
<div class="abs serif" style="left:430px;top:4705px;width:340px;text-align:center;font-size:34px;color:var(--gold);display:flex;align-items:center;justify-content:center;gap:12px"><span style="width:18px;height:18px;border-radius:50%;background:var(--gold)"></span>WestaKolory</div>
<h4 style="left:831px;top:4676px" class="footer-title">FOLLOW US</h4>
<div class="social" style="left:832px"></div>
<div class="social" style="left:877px"></div>
<div class="social" style="left:921px"></div>
<div class="social" style="left:965px"></div>
<div class="social" style="left:1010px"></div>
<div class="social" style="left:1054px"></div>
<p class="abs" style="left:0;top:4896px;width:1200px;text-align:center;color:#fff;font-size:12px">© Copyright 2025. All Rights Reserved</p>
<div class="abs" style="left:1134px;top:4874px;width:40px;height:40px;border-radius:50%;background:var(--gold);display:flex;align-items:center;justify-content:center"><svg width="10" height="7"><path d="M1 6l4-4 4 4" stroke="#fff" fill="none" stroke-width="1.5"/></svg></div>
</body>
</html>
```